Professionelles Social Media Material für Reinigungsdienstleister
Zielgruppe
Wir reinigen Privathaushalte, Ferienwohnungen, Arztpraxen und Büroräume.
Aufgabenstellung
Ich wünsche Material für ein professionelles Auftreten bei Facebook und Instagram. Wir müssen bei Facebook leider neu starten und haben Instagram bei dieser Firma bisher vernachlässigt.
Nun wollen wir unser Social Media professionell erscheinen lassen und einen Plan für die kommenden 2 Monate erstellen. Wir suchen dafür mindestens 20 passende Postings und die Inhalte für den Start.
Nachtrag zu den Postings: Wir wollen ganz allgemeinen Content und sind offen für alle Vorschläge. Es kann gern auch eine Sommeraktion beworben werden, bei der wir Neukunden 100€ schenken und eine Aktion, bei der es eine kostenlose Erstreinigung gibt um unsere Leistung zu testen.

```html
<!DOCTYPE html>
<html lang="de">
<head>
<meta charset="utf-8">
<title>Wohnglanz Pilot – Social Media Postings</title>
<link rel="stylesheet" href="https://fonts.googleapis.com/css2?family=Lexend:wght@500;600;700&family=Poppins:wght@400;500;600&display=swap">
<style>
:root{
  --board:#e8e8e8;
  --navy:#4a5b8b;
  --navy-dark:#3d4d7a;
  --cyan:#3ea8cb;
  --ice:#e3edf7;
  --ice-2:#c9dcee;
  --white:#ffffff;
  --yellow:#f1c21b;
}
*{box-sizing:border-box;margin:0;padding:0}
html,body{width:785px;height:1200px;overflow:hidden;background:var(--board)}
body{position:relative;font-family:"Poppins",sans-serif;color:var(--navy)}
.post{position:absolute;width:206px;height:257px;overflow:hidden}
.col-1{left:66px}.col-2{left:290px}.col-3{left:514px}
.row-1{top:60px}.row-2{top:335px}.row-3{top:610px}.row-4{top:885px}
.navy{background:var(--navy)}
.ice{background:linear-gradient(180deg,#eef4fa,#d6e5f3)}
.white{background:var(--white)}
.abs{position:absolute}
.h{font-family:"Lexend",sans-serif;font-weight:700;line-height:1.05}
.accent{color:var(--cyan)}
.logo-disc{position:absolute;width:64px;height:64px;border-radius:50%;background:var(--white);border:1.5px solid var(--cyan);display:flex;align-items:center;justify-content:center;text-align:center}
.logo-name{display:block;font-family:"Lexend",sans-serif;font-weight:600;font-size:6.5px;line-height:1.15;color:var(--navy)}
.disc-tr{right:-14px;top:-14px;padding:10px 8px 0 0}
.disc-tl{left:-14px;top:-14px;padding:10px 0 0 8px}
.disc-br{right:-10px;bottom:-12px;padding:0 6px 8px 0}
.top-logo{position:absolute;left:0;right:0;top:26px;text-align:center}
.contact-bar{position:absolute;left:8px;right:8px;bottom:8px;height:12px;border-radius:6px;background:var(--white);border:1px solid var(--ice-2);display:flex;align-items:center;justify-content:space-around;font-size:4.1px;font-weight:600;color:var(--navy)}
.contact-bar span{display:flex;align-items:center;gap:2px}
.dot{width:5px;height:5px;border-radius:50%;border:1px solid var(--cyan);display:inline-block}
.call-pill{position:absolute;left:12px;bottom:9px;height:13px;padding:0 8px;border-radius:7px;background:var(--white);border:1px solid var(--ice-2);display:flex;align-items:center;gap:3px;font-family:"Lexend",sans-serif;font-weight:600;font-size:6.3px;color:var(--navy)}
.call-pill .dot{width:6px;height:6px;background:var(--cyan);border:none}
.photo{position:absolute}
.tag{position:absolute;background:var(--white);border:1px solid var(--navy);border-radius:3px;box-shadow:1.5px 1.5px 0 var(--navy);padding:2px 5px;font-size:4.8px;line-height:1.25;text-align:center;color:var(--navy)}
.navy .tag{border-color:var(--white);box-shadow:1.5px 1.5px 0 var(--cyan)}
.der-pill{background:var(--cyan);color:var(--white);border-radius:4px;font-family:"Lexend",sans-serif;font-weight:700;font-size:13px;padding:1px 4px;transform:rotate(-6deg)}
.bubble-box{position:absolute;background:var(--navy);color:var(--white);border:1.5px solid var(--cyan);border-radius:7px;font-family:"Lexend",sans-serif;font-weight:600;text-align:center;line-height:1.05}
.benefit{position:absolute;display:flex;gap:6px;align-items:flex-start;width:128px}
.benefit .icon{flex:0 0 22px;height:22px;border-radius:50%;background:var(--cyan);display:flex;align-items:center;justify-content:center}
.benefit b{display:block;font-size:4.8px;font-weight:600;color:var(--white);letter-spacing:.1px}
.benefit p{font-size:4.6px;line-height:1.6;color:#dfe6f4}
</style>
</head>
<body>

<!-- Row 1 -->
<section class="post navy col-1 row-1">
  <div class="logo-disc disc-tr"><span class="logo-name">Wohnglanz<br>Pilot</span></div>
  <div class="abs der-pill" style="left:14px;top:24px">Der</div>
  <div class="abs h" style="left:54px;top:24px;font-size:15.5px;color:var(--white)">GEWERBE<br>PILOT!</div>
  <p class="abs" style="left:54px;top:67px;width:120px;font-size:5.6px;line-height:1.85;font-weight:500;color:var(--white)">Wir bieten professionelle Reinigungsdienstleistungen für Unternehmen an. Unsere erfahrenen Reinigungskräfte sind speziell geschult und sorgen für Sauberkeit und Hygiene in Ihren Geschäftsräumen.</p>
  <svg class="photo" role="img" aria-label="Foto: zwei Reinigungskräfte in Latzhosen wischen Schreibtische in einem Büro" style="left:0;top:136px" width="206" height="121" viewBox="0 0 206 121">
    <defs><linearGradient id="office" x1="0" y1="0" x2="1" y2="1"><stop offset="0" stop-color="#eef2f6"/><stop offset="1" stop-color="#8a98b0"/></linearGradient></defs>
    <path d="M0 34 C40 10 110 2 206 12 L206 121 L0 121Z" fill="url(#office)"/>
    <path d="M0 34 C40 10 110 2 206 12" fill="none" stroke="#3ea8cb" stroke-width="3"/>
  </svg>
  <div class="abs" style="left:16px;top:139px;width:46px;height:46px;border-radius:50%;background:#7fb7d6;border:2px solid var(--white)"></div>
  <div class="contact-bar"><span><i class="dot"></i>0157 400 22 318</span><span><i class="dot"></i>info@wohnglanzpilot.de</span><span><i class="dot"></i>www.wohnglanzpilot.de</span></div>
</section>

<section class="post ice col-2 row-1">
  <div class="abs" role="img" aria-label="Blasses Foto: Reinigungsteam in Schutzkleidung im Hintergrund" style="inset:0;background:linear-gradient(160deg,rgba(255,255,255,.5),rgba(190,210,230,.4))"></div>
  <div class="abs h" style="left:0;right:0;top:19px;text-align:center;font-size:11.5px;font-weight:600;color:var(--navy)">Zu den Aufgaben eines<br><span class="accent" style="font-weight:700">GEWERBE PILOTEN</span><br>gehören z.B.</div>
  <div class="tag" style="left:28px;top:76px;transform:rotate(4deg)">Reinigung von Büroräumen,<br>Fluren und Sanitäranlagen</div>
  <div class="tag" style="left:28px;top:116px;transform:rotate(2deg)">Fensterreinigung (Innen-<br>und Außenbereich)</div>
  <div class="tag" style="left:111px;top:112px;transform:rotate(-5deg)">Bodenreinigung und -pflege<br>(Teppich, Fliesen, Holz)</div>
  <div class="tag" style="left:118px;top:147px;transform:rotate(-6deg)">Entfernung von Staub<br>und Schmutz</div>
  <div class="tag" style="left:33px;top:166px;transform:rotate(3deg)">Entsorgung von<br>Abfällen und Müll</div>
  <div class="call-pill">Jetzt anrufen <i class="dot"></i> 0157 400 22 318</div>
  <div class="logo-disc disc-br"><span class="logo-name">Wohnglanz<br>Pilot</span></div>
</section>

<section class="post navy col-3 row-1">
  <div class="logo-disc disc-tl"><span class="logo-name">Wohnglanz<br>Pilot</span></div>
  <div class="abs h" style="left:66px;top:14px;font-size:29px;color:var(--cyan)">4</div>
  <div class="abs h" style="left:91px;top:16px;font-size:10.5px;line-height:1.25;font-weight:600;color:var(--white);white-space:nowrap"><span class="accent">Vorteile</span> bringt<br>die Nutzung des<br><span class="accent">GEWERBE PILOTEN</span></div>
  <div class="benefit" style="left:26px;top:75px"><span class="icon"><svg width="12" height="12" viewBox="0 0 12 12"><circle cx="6" cy="6" r="4.5" fill="none" stroke="#fff" stroke-width="1.2"/></svg></span><div><b>PROFESSIONELLE EXPERTISE</b><p>Professionelle und vertrauenswürdige Reinigungskräfte.</p></div></div>
  <div class="benefit" style="left:68px;top:112px"><span class="icon"><svg width="12" height="12" viewBox="0 0 12 12"><path d="M6 11V5M6 5L3 2M6 5l3-3" fill="none" stroke="#fff" stroke-width="1.2"/></svg></span><div><b>FLEXIBILITÄT</b><p>Dienstleistungen, die sich an Ihre Bedürfnisse anpassen.</p></div></div>
  <div class="benefit" style="left:26px;top:144px"><span class="icon"><svg width="12" height="12" viewBox="0 0 12 12"><path d="M2.5 6.5l2.5 2.5 4.5-5" fill="none" stroke="#fff" stroke-width="1.3"/></svg></span><div><b>QUALITÄT</b><p>Hochwertige<br>Reinigungsdienstleistungen.</p></div></div>
  <div class="benefit" style="left:68px;top:181px"><span class="icon"><svg width="12" height="12" viewBox="0 0 12 12"><path d="M6 11C2 8 2 4 6 1c4 3 4 7 0 10zM6 11V5" fill="none" stroke="#fff" stroke-width="1.1"/></svg></span><div><b>UMWELTFREUNDLICH</b><p>Verwendung umweltfreundlicher Reinigungsmittel.</p></div></div>
  <div class="contact-bar"><span><i class="dot"></i>0157 400 22 318</span><span><i class="dot"></i>info@wohnglanzpilot.de</span><span><i class="dot"></i>www.wohnglanzpilot.de</span></div>
</section>

<!-- Row 2 -->
<section class="post ice col-1 row-2">
  <div class="photo" role="img" aria-label="Foto: Wischmopp auf hellem Parkettboden" style="left:0;top:0;width:206px;height:86px;background:linear-gradient(180deg,#c8d3de,#e9eef3 70%,#3ea8cb 92%,#eef4fa)"></div>
  <div class="logo-disc disc-tl"><span class="logo-name">Wohnglanz<br>Pilot</span></div>
  <div class="abs der-pill" style="left:22px;top:93px">Der</div>
  <div class="abs h" style="left:60px;top:92px;font-size:15.5px;color:var(--navy)">HAUSHALTS<br>PILOT!</div>
  <p class="abs" style="left:24px;top:136px;font-size:5.7px;line-height:1.85;font-weight:500;color:var(--navy)">Das bisschen Haushalt macht sich von allein…<br>Du brauchst nur den richtigen Helden!</p>
  <div class="photo" role="img" aria-label="Foto: Eimer mit Putzmitteln, Sprühflaschen und Putzlappen" style="left:12px;top:168px;width:66px;height:72px;border-radius:8px;background:radial-gradient(circle at 50% 60%,#5fb8dc,#cfe2f1 70%,transparent 72%)"></div>
  <div class="bubble-box" style="left:90px;top:166px;width:111px;height:54px;transform:rotate(3deg);border:none;padding:10px 8px;font-family:'Poppins',sans-serif;font-weight:500;font-size:5.8px;line-height:1.7">Ein <span class="accent">WOHNGLANZ PILOT</span> ist ein Held, der dich bei der Reinigung und Organisation des Haushalts unterstützt.</div>
  <div class="contact-bar"><span><i class="dot"></i>0157 400 22 318</span><span><i class="dot"></i>info@wohnglanzpilot.de</span><span><i class="dot"></i>www.wohnglanzpilot.de</span></div>
</section>

<section class="post navy col-2 row-2">
  <div class="abs h" style="left:0;right:0;top:19px;text-align:center;font-size:11.5px;font-weight:600;color:var(--white)">Zu den Aufgaben eines<br><span class="accent" style="font-weight:700">HAUSHALTS PILOTEN</span><br>gehören z.B.</div>
  <div class="tag" style="left:18px;top:68px;transform:rotate(5deg)">Reinigung von Böden, Fenstern,<br>Möbeln und Sanitäranlagen</div>
  <div class="tag" style="left:112px;top:88px;transform:rotate(-4deg)">Staubsaugen, Staubwischen<br>und Abstauben</div>
  <div class="tag" style="left:24px;top:101px;transform:rotate(3deg)">Wäsche waschen,<br>trocknen und bügeln</div>
  <div class="tag" style="left:99px;top:118px;transform:rotate(-6deg)">Betten machen und<br>Zimmer aufräumen</div>
  <div class="tag" style="left:16px;top:136px;transform:rotate(4deg)">Einkaufen und<br>Besorgungen erledigen</div>
  <div class="tag" style="left:130px;top:146px;transform:rotate(-5deg)">Zubereitung von<br>Mahlzeiten</div>
  <div class="tag" style="left:53px;top:162px">Reinigung der Küche</div>
  <div class="tag" style="left:51px;top:186px;transform:rotate(-3deg)">Gartenarbeit wie Rasenmähen,<br>Unkraut jäten und Pflanzenpflege</div>
  <div class="call-pill">Jetzt anrufen <i class="dot"></i> 0157 400 22 318</div>
  <div class="logo-disc disc-br"><span class="logo-name">Wohnglanz<br>Pilot</span></div>
</section>

<section class="post ice col-3 row-2" style="background:linear-gradient(180deg,#ffffff 40%,#dbe9f5)">
  <div class="logo-disc disc-tr"><span class="logo-name">Wohnglanz<br>Pilot</span></div>
  <div class="abs h" style="left:20px;top:18px;font-size:11.5px;line-height:1.25;font-weight:600;color:var(--navy)">Was macht einen<br>echten <span class="accent">HAUSHALTS</span><br><span class="accent">PILOTEN</span> aus?</div>
  <div class="photo" role="img" aria-label="Foto: Hand im gelben Gummihandschuh hält blauen Putzeimer mit Schwämmen" style="left:150px;top:52px;width:56px;height:190px;background:linear-gradient(200deg,#f3d23a 0,#e8c52a 30%,#cdd9e6 55%,#3d8fd0 85%)"></div>
  <div class="abs" style="left:21px;top:70px;width:128px;font-size:5.1px;line-height:1.9;font-weight:600;color:var(--navy)">
    <p style="margin-bottom:6px">Was macht einen echten HAUSHALTS PILOTEN aus? Er zeichnet sich durch Zuverlässigkeit, Gründlichkeit und Diskretion aus.</p>
    <p style="margin-bottom:6px">Er arbeitet selbstständig und erledigt seine Aufgaben effizient und sorgfältig. Dabei geht er auf die individuellen Bedürfnisse und Wünsche der Familie ein und passt sich flexibel an.</p>
    <p>Er kann sowohl regelmäßig als auch gelegentlich gebucht werden und ist eine wertvolle Unterstützung für Familien und Berufstätige, die wenig Zeit für die Hausarbeit haben.</p>
  </div>
  <div class="contact-bar"><span><i class="dot"></i>0157 400 22 318</span><span><i class="dot"></i>info@wohnglanzpilot.de</span><span><i class="dot"></i>www.wohnglanzpilot.de</span></div>
</section>

<!-- Row 3 -->
<section class="post navy col-1 row-3">
  <div class="abs h" style="left:0;right:0;top:16px;text-align:center;font-size:16px;font-weight:600;color:var(--white)">Öffnungszeiten</div>
  <div class="abs" style="left:30px;top:46px;width:140px;height:160px;background:var(--white);border-radius:6px;box-shadow:4px 4px 0 var(--cyan);transform:rotate(-2deg);padding:12px 10px">
    <table style="width:100%;border-collapse:collapse;font-size:6.5px;font-weight:500;color:var(--navy)">
      <tr style="border-bottom:.6px solid var(--navy)"><td style="padding:3.5px 0"><span class="accent">→</span> Montag:</td><td style="text-align:right">7:00 – 20:00 Uhr</td></tr>
      <tr style="border-bottom:.6px solid var(--navy)"><td style="padding:3.5px 0"><span class="accent">→</span> Dienstag:</td><td style="text-align:right">7:00 – 20:00 Uhr</td></tr>
      <tr style="border-bottom:.6px solid var(--navy)"><td style="padding:3.5px 0"><span class="accent">→</span> Mittwoch:</td><td style="text-align:right">7:00 – 20:00 Uhr</td></tr>
      <tr style="border-bottom:.6px solid var(--navy)"><td style="padding:3.5px 0"><span class="accent">→</span> Donnerstag:</td><td style="text-align:right">7:00 – 20:00 Uhr</td></tr>
      <tr style="border-bottom:.6px solid var(--navy)"><td style="padding:3.5px 0"><span class="accent">→</span> Freitag:</td><td style="text-align:right">7:00 – 20:00 Uhr</td></tr>
      <tr style="border-bottom:.6px solid var(--navy)"><td style="padding:3.5px 0"><span class="accent">→</span> Samstag:</td><td style="text-align:right">7:00 – 20:00 Uhr</td></tr>
      <tr style="border-bottom:.6px solid var(--navy)"><td style="padding:3.5px 0"><span class="accent">→</span> Sonntag:</td><td style="text-align:right">7:00 – 20:00 Uhr</td></tr>
    </table>
  </div>
  <div class="photo" role="img" aria-label="Foto: gelber Gummihandschuh mit grauem Putztuch" style="left:0;top:176px;width:70px;height:81px;border-radius:0 40px 0 0;background:linear-gradient(150deg,#8fa3b8 0,#e9c428 45%,#f1c21b)"></div>
  <div class="call-pill">Jetzt anrufen <i class="dot"></i> 0157 400 22 318</div>
  <div class="logo-disc disc-br"><span class="logo-name">Wohnglanz<br>Pilot</span></div>
</section>

<section class="post white col-2 row-3">
  <div class="abs h" style="left:0;right:0;top:16px;text-align:center;font-size:15px;font-weight:600;color:var(--navy)">Keine Zeit<br>für die <span class="accent">Reinigung?</span></div>
  <div class="photo" role="img" aria-label="Foto: Reinigungskraft mit Besen und Eimer voller Putzmittel, umgeben von gezeichneten Putzsymbolen" style="left:20px;top:84px;width:186px;height:173px;background:radial-gradient(ellipse at 50% 55%,#cfe6f4 0,#eaf3fa 55%,#ffffff 75%)"></div>
  <div class="bubble-box" style="left:14px;top:62px;width:80px;height:38px;transform:rotate(-5deg);padding:6px 4px;font-size:11px">Überlassen<br>Sie es uns!</div>
  <div class="call-pill">Jetzt anrufen <i class="dot"></i> 0157 400 22 318</div>
  <div class="logo-disc disc-br"><span class="logo-name">Wohnglanz<br>Pilot</span></div>
</section>

<section class="post navy col-3 row-3">
  <div class="abs h" style="left:0;right:0;top:15px;text-align:center;font-size:16px;font-weight:600;color:var(--white)">Was sagt der<br><span class="accent">Kunde?</span></div>
  <div class="abs" style="left:35px;top:62px;width:140px;height:72px;background:var(--white);border-radius:7px;transform:rotate(1deg);padding:8px 12px">
    <div style="display:flex;justify-content:space-between;align-items:center">
      <span style="color:var(--yellow);font-size:7px;letter-spacing:1px">★★★★★</span>
      <span style="font-family:'Lexend',sans-serif;font-weight:600;font-size:6.5px;color:var(--navy)">Bewertung</span>
    </div>
    <p style="margin-top:4px;font-size:4.5px;line-height:1.6;font-style:italic;color:var(--navy)">Die erbrachten Leistungen sind zu unserer vollsten Zufriedenheit durchgeführt wurden. Wir sind sehr zufrieden mit dem Piloten Team und der Freundlichkeit dieses dynamischen Unternehmens. Auf weitere gute und lange Zusammenarbeit.</p>
    <p style="text-align:right;font-size:4.8px;font-weight:600;margin-top:2px">Jonas Reker</p>
  </div>
  <div class="photo" role="img" aria-label="Foto: erstaunte junge Frau mit braunem Haar blickt zur Seite" style="left:56px;top:140px;width:100px;height:117px;border-radius:50px 50px 0 0;background:linear-gradient(180deg,#8a5a3c,#e7b9a0 50%,#d9a58c)"></div>
  <div class="call-pill">Jetzt anrufen <i class="dot"></i> 0157 400 22 318</div>
  <div class="logo-disc disc-br"><span class="logo-name">Wohnglanz<br>Pilot</span></div>
</section>

<!-- Row 4 -->
<section class="post white col-1 row-4">
  <div class="top-logo"><span class="logo-name">Wohnglanz<br>Pilot</span></div>
  <div class="abs h" style="left:0;right:0;top:50px;text-align:center;font-size:11.5px;line-height:1.25;font-weight:600;color:var(--navy)">Brauche Hilfe für<br><span style="font-weight:700;font-size:12.5px">GEWERBE<span class="accent">REINIGUNG?</span></span></div>
  <div class="photo" role="img" aria-label="Foto: Reinigungsteam in blauen Schürzen legt die Hände übereinander" style="left:0;top:84px;width:206px;height:173px;background:linear-gradient(180deg,#f4f6f8,#b9d4e8 60%,#5f8fb8)"></div>
  <div class="bubble-box" style="left:48px;top:90px;width:96px;height:40px;transform:rotate(-5deg);padding:6px 4px;font-size:11px">Wir können<br>Ihnen helfen</div>
  <div class="bubble-box" style="left:78px;top:182px;width:86px;height:38px;transform:rotate(5deg);padding:6px 4px;font-size:11px">Wir machen<br>das alles</div>
  <div class="contact-bar"><span><i class="dot"></i>0157 400 22 318</span><span><i class="dot"></i>info@wohnglanzpilot.de</span><span><i class="dot"></i>www.wohnglanzpilot.de</span></div>
</section>

<section class="post navy col-2 row-4">
  <div class="abs" style="left:45px;top:70px;width:116px;height:116px;border-radius:50%;background:rgba(255,255,255,.18);border:1px solid rgba(255,255,255,.5)"></div>
  <div class="abs" style="left:53px;top:78px;width:100px;height:100px;border-radius:50%;background:var(--white);display:flex;align-items:center;justify-content:center;text-align:center">
    <span class="logo-name" style="font-size:11.5px">Wohnglanz<br>Pilot</span>
  </div>
</section>

<section class="post white col-3 row-4">
  <div class="top-logo"><span class="logo-name">Wohnglanz<br>Pilot</span></div>
  <div class="abs h" style="left:0;right:0;top:50px;text-align:center;font-size:11.5px;line-height:1.25;font-weight:600;color:var(--navy)">Brauche Hilfe für<br><span style="font-weight:700;font-size:12.5px">HAUSHALTS<span class="accent">REINIGUNG?</span></span></div>
  <div class="photo" role="img" aria-label="Foto: lächelnde Haushaltshilfe wischt mit blauem Tuch einen Tisch" style="left:0;top:84px;width:206px;height:173px;background:linear-gradient(180deg,#f2f4f6,#e8dccd 55%,#b99b7a)"></div>
  <div class="bubble-box" style="left:22px;top:98px;width:96px;height:40px;transform:rotate(-5deg);padding:6px 4px;font-size:11px">Wir können<br>Ihnen helfen</div>
  <div class="bubble-box" style="left:48px;top:168px;width:86px;height:38px;transform:rotate(5deg);padding:6px 4px;font-size:11px">Wir machen<br>das alles</div>
  <div class="contact-bar"><span><i class="dot"></i>0157 400 22 318</span><span><i class="dot"></i>info@wohnglanzpilot.de</span><span><i class="dot"></i>www.wohnglanzpilot.de</span></div>
</section>

</body>
</html>
```